GIN BOTTLE LOGO NEED IT TO MATCH THE DESIGN FOR MORVA CREST IMAGE AS THEY ARE SISTER BRANDS. I'VE ATTACHED IMAGES OF TELBA (THE IMAGES ARE JUST FOR REFERENCE)

Logo Text

TELBA

```html
<!DOCTYPE html>
<html lang="en">
<head>
<meta charset="utf-8">
<title>TELBA Gin Label</title>
<link rel="stylesheet" href="https://fonts.googleapis.com/css2?family=EB+Garamond:wght@500&family=Righteous&display=swap">
<style>
  :root {
    --backdrop: #ece8ea;
    --label-light: #9a6b67;
    --label-mid: #74393a;
    --label-dark: #52262a;
    --gold: #b98a55;
    --ink-white: #fbf6f2;
    --portrait-tone: #f3e6e2;
  }
  html, body {
    margin: 0;
    padding: 0;
    width: 846px;
    height: 1200px;
    overflow: hidden;
    background: var(--backdrop);
  }
  .canvas {
    position: relative;
    width: 846px;
    height: 1200px;
  }
  .label {
    position: absolute;
    left: 103px;
    top: 142px;
    width: 640px;
    height: 915px;
  }
  .label-body { fill: url(#labelShade); }
  .label-frame {
    fill: none;
    stroke: var(--gold);
    stroke-width: 3;
  }
  .arched-title {
    font-family: "EB Garamond", "Times New Roman", serif;
    font-weight: 500;
    font-size: 48px;
    letter-spacing: 4px;
    fill: var(--ink-white);
  }
  .portrait-area { fill: var(--portrait-tone); opacity: 0.22; }
  .name-rule { stroke: var(--gold); stroke-width: 2; }
  .brand-name {
    font-family: "Righteous", "Arial", sans-serif;
    font-size: 74px;
    letter-spacing: 2px;
    fill: var(--ink-white);
  }
  .flourish-area { fill: var(--gold); opacity: 0.4; }
</style>
</head>
<body>
<div class="canvas">
  <svg class="label" viewBox="0 0 640 915" xmlns="http://www.w3.org/2000/svg">
    <defs>
      <linearGradient id="labelShade" x1="1" y1="0" x2="0" y2="1">
        <stop offset="0" style="stop-color: var(--label-light)"/>
        <stop offset="0.5" style="stop-color: var(--label-mid)"/>
        <stop offset="1" style="stop-color: var(--label-dark)"/>
      </linearGradient>
      <path id="titleArc" d="M46,372 A274,274 0 0 1 594,372"/>
    </defs>

    <path class="label-body" d="M0,330 C0,120 140,0 320,0 C500,0 640,120 640,330 V915 H0 Z"/>
    <path class="label-frame" d="M16,335 C16,132 150,16 320,16 C490,16 624,132 624,335 V899 H16 Z"/>

    <text class="arched-title">
      <textPath href="#titleArc" startOffset="50%" text-anchor="middle">DISTILLED IRISH GIN</textPath>
    </text>

    <rect class="flourish-area" x="30" y="380" width="8" height="150" rx="4" role="img" aria-label="Left side scroll ornament"/>
    <rect class="flourish-area" x="602" y="380" width="8" height="150" rx="4" role="img" aria-label="Right side scroll ornament"/>

    <path class="portrait-area" role="img" aria-label="Engraved portrait illustration framed by a patterned arch"
      d="M80,560 L80,400 A240,230 0 0 1 560,400 L560,560 L480,600 A170,110 0 0 1 160,600 Z"/>

    <line class="name-rule" x1="210" y1="672" x2="430" y2="672"/>
    <text class="brand-name" x="320" y="748" text-anchor="middle">TELBA</text>

    <rect class="flourish-area" x="140" y="772" width="360" height="40" rx="20" role="img" aria-label="Gold scroll flourish ornament"/>
    <rect class="flourish-area" x="30" y="790" width="8" height="90" rx="4" role="img" aria-label="Lower left corner flourish"/>
    <rect class="flourish-area" x="602" y="790" width="8" height="90" rx="4" role="img" aria-label="Lower right corner flourish"/>
  </svg>
</div>
</body>
</html>
```